Design New Vehicle Graphics for new company

We have 5 vehicles to get new vehicle raps on based on our new company name. HPG is it.
It stands for Haverlane Pumping Group.
Our website is haverlanepumpinggroup.ie.
We have three KL drovetts
We have a KL Ostrelo
We also have a KL Pell
All of these are to be wrapped.

I would like the followings texts to be used if possible.
Design Build Maintain
Water Pumps
Wastewater Pumps
Water Treatment
Irrigation
Water Softeners
Rainwater Harvesting
Leak Detection

Phone: 041 7730194
Website: haverlanepumpinggroup.ie
Email: info@haverlanepumpinggroup.ie

Target Market(s)

Everybody

Industry/Entity Type

Utilities

Requirements
Must have
• **The vehicles are in a dark grey and we want to incorporate this at the front so it is more of a half warp

```html
<!DOCTYPE html>
<html lang="en">
<head>
<meta charset="utf-8">
<title>Haverlane Pumping Group – Van Side Wrap</title>
<link rel="stylesheet" href="https://fonts.googleapis.com/css2?family=Montserrat:ital,wght@0,600;0,700;1,800&family=Quicksand:wght@700&display=swap">
<style>
  :root {
    --backdrop: #8b7550;
    --van-grey: #3c3c3e;
    --van-grey-dark: #2a2a2c;
    --trim: #232325;
    --glass: #5a5246;
    --navy: #0c3856;
    --navy-deep: #06263c;
    --silver: #d9dadc;
    --white: #ffffff;
    --tyre: #1e1e20;
    --rim: #c8c9cb;
    --lamp: #6e1a1d;
  }
  html, body {
    margin: 0;
    padding: 0;
    width: 1200px;
    height: 675px;
    overflow: hidden;
    background: var(--backdrop);
  }
  .wrap-canvas { display: block; width: 1200px; height: 675px; }
  .ground-shadow { fill: #000; opacity: .28; }
  .van-body { fill: var(--van-grey); }
  .van-glass { fill: var(--glass); }
  .van-trim { fill: var(--trim); }
  .panel-seam { fill: none; stroke: var(--van-grey-dark); stroke-width: 1.5; }
  .rear-lamp { fill: var(--lamp); }
  .head-lamp { fill: #b9bcc0; }
  .rear-field { fill: var(--navy); }
  .rear-shade { fill: var(--navy-deep); opacity: .6; }
  .band-edge { fill: none; stroke: var(--silver); stroke-width: 3; }
  .tyre { fill: var(--tyre); }
  .rim { fill: var(--rim); }
  .rim-hub { fill: #8d8f92; }
  .rim-slot { fill: #4a4b4e; }
  .company-rule { stroke: var(--silver); stroke-width: 3; }
  .company-name {
    font-family: "Montserrat", sans-serif; font-weight: 600;
    font-size: 24px; fill: var(--silver); letter-spacing: .5px;
  }
  .brand-name {
    font-family: "Montserrat", sans-serif; font-weight: 700;
    font-size: 48px; fill: var(--white); letter-spacing: 1px;
  }
  .service-item {
    font-family: "Quicksand", sans-serif; font-weight: 700;
    font-size: 12.5px; fill: var(--white);
  }
  .service-bullet { fill: none; stroke: var(--white); stroke-width: 1.6; }
  .pillar-label {
    font-family: "Montserrat", sans-serif; font-weight: 600;
    font-size: 12.5px; fill: var(--white);
  }
  .pillar-icon { fill: none; stroke: var(--white); stroke-width: 1.5; }
  .phone-number {
    font-family: "Montserrat", sans-serif; font-weight: 800; font-style: italic;
    font-size: 29.5px; fill: var(--white);
  }
  .phone-badge { fill: var(--white); }
  .phone-glyph { fill: var(--navy); }
  .web-address {
    font-family: "Montserrat", sans-serif; font-weight: 600;
    font-size: 24px; fill: var(--silver); letter-spacing: 1px;
  }
</style>
</head>
<body>
<svg class="wrap-canvas" viewBox="0 0 1200 675" xmlns="http://www.w3.org/2000/svg" aria-label="Haverlane Pumping Group side van wrap">
  <defs>
    <radialGradient id="shadow-fade">
      <stop offset="0" stop-color="#000" stop-opacity="1"/>
      <stop offset="1" stop-color="#000" stop-opacity="0"/>
    </radialGradient>
    <clipPath id="van-outline">
      <path d="M90,452 L88,395 Q92,340 140,315 L250,262 L372,152 Q385,140 410,137 L1040,128 Q1056,129 1060,145 L1086,290 L1092,405 L1104,425 L1104,450 L1000,458 A76,76 0 0 0 848,460 L322,462 A76,76 0 0 0 170,462 Z"/>
    </clipPath>
  </defs>

  <ellipse class="ground-shadow" cx="600" cy="516" rx="530" ry="16" fill="url(#shadow-fade)"/>

  <!-- vehicle body -->
  <path class="van-body" d="M90,452 L88,395 Q92,340 140,315 L250,262 L372,152 Q385,140 410,137 L1040,128 Q1056,129 1060,145 L1086,290 L1092,405 L1104,425 L1104,450 L1000,458 A76,76 0 0 0 848,460 L322,462 A76,76 0 0 0 170,462 Z"/>

  <g clip-path="url(#van-outline)">
    <!-- windscreen edge and driver window -->
    <path class="van-trim" d="M252,262 L372,152 L382,152 L268,262 Z"/>
    <path class="van-glass" d="M328,262 L388,176 Q398,163 414,162 L492,161 L492,264 Z"/>
    <path class="panel-seam" d="M290,270 L290,460 M512,150 L512,460 M524,156 L612,154 L612,265 L524,265 Z"/>
    <path class="panel-seam" d="M456,286 L490,286"/>

    <!-- navy rear field and lower band -->
    <path class="rear-field" d="M655,120 L1120,120 L1120,480 L316,480 L316,422 Q430,394 560,412 Q690,418 745,360 C790,300 740,200 655,120 Z"/>
    <path class="rear-shade" d="M1000,120 L1120,120 L1120,480 L1050,480 C1080,380 1070,220 1000,120 Z"/>
    <path class="band-edge" d="M316,421 Q430,393 560,411 Q610,414 645,410"/>

    <!-- lower trim -->
    <rect class="van-trim" x="80" y="405" width="70" height="55"/>
    <rect class="van-trim" x="1000" y="405" width="110" height="45"/>
  </g>

  <!-- lamps and mirror -->
  <path class="head-lamp" d="M100,330 L172,316 L160,348 L98,352 Z"/>
  <rect class="rear-lamp" x="1064" y="292" width="18" height="56" rx="3"/>
  <path class="van-trim" d="M296,276 Q292,252 312,240 L330,238 L332,276 Z"/>

  <!-- wheels -->
  <g class="wheel">
    <circle class="tyre" cx="246" cy="456" r="66"/>
    <circle class="rim" cx="246" cy="456" r="44"/>
    <circle class="rim-hub" cx="246" cy="456" r="7"/>
  </g>
  <g class="wheel">
    <circle class="tyre" cx="924" cy="456" r="66"/>
    <circle class="rim" cx="924" cy="456" r="44"/>
    <circle class="rim-hub" cx="924" cy="456" r="7"/>
  </g>

  <!-- company name -->
  <line class="company-rule" x1="335" y1="311" x2="335" y2="397"/>
  <text class="company-name" x="349" y="338">HAVERLANE</text>
  <text class="company-name" x="349" y="362">PUMPING</text>
  <text class="company-name" x="349" y="386">GROUP</text>

  <!-- brand name -->
  <text class="brand-name" x="622" y="342" text-anchor="middle">HPG</text>

  <!-- services -->
  <g class="service-list">
    <circle class="service-bullet" cx="822" cy="157" r="3.5"/><text class="service-item" x="831" y="161">Water Pumps</text>
    <circle class="service-bullet" cx="822" cy="172.5" r="3.5"/><text class="service-item" x="831" y="176.5">Wastewater Pumps</text>
    <circle class="service-bullet" cx="822" cy="188" r="3.5"/><text class="service-item" x="831" y="192">Water Treatment</text>
    <circle class="service-bullet" cx="822" cy="203.5" r="3.5"/><text class="service-item" x="831" y="207.5">Irrigation</text>
    <circle class="service-bullet" cx="822" cy="219" r="3.5"/><text class="service-item" x="831" y="223">Water Softeners</text>
    <circle class="service-bullet" cx="822" cy="234.5" r="3.5"/><text class="service-item" x="831" y="238.5">Rainwater Harvesting</text>
    <circle class="service-bullet" cx="822" cy="250" r="3.5"/><text class="service-item" x="831" y="254">Leak Detection</text>
  </g>

  <!-- design build maintain -->
  <g class="pillars">
    <circle class="pillar-icon" cx="796" cy="275" r="10.5"/>
    <path class="pillar-icon" d="M790,269 L802,281 M802,269 L790,281"/>
    <text class="pillar-label" x="810" y="280">DESIGN</text>
    <circle class="pillar-icon" cx="883" cy="273" r="10.5"/>
    <path class="pillar-icon" d="M878,268 L889,279 M876,270 L881,265"/>
    <text class="pillar-label" x="898" y="278">BUILD</text>
    <circle class="pillar-icon" cx="961" cy="272" r="10.5"/>
    <path class="pillar-icon" d="M955,266 L967,278 M967,266 L955,278"/>
    <text class="pillar-label" x="976" y="277">MAINTAIN</text>
  </g>

  <!-- phone -->
  <circle class="phone-badge" cx="799" cy="330" r="13"/>
  <path class="phone-glyph" d="M793,322 q-3,3 0,9 q4,7 10,8 q3,0 4,-2 l-3,-3 q-2,1 -3,0 q-3,-2 -4,-5 q0,-1 1,-2 l-3,-5 Z"/>
  <text class="phone-number" x="828" y="340">(041) 7730194</text>

  <!-- website -->
  <text class="web-address" x="386" y="445">www.haverlanepumpinggroup.ie</text>
</svg>
</body>
</html>
```